Business cards to launch an education platform

Hi,
I am looking at having new business cards designed.
I am a startup, developing a web platform for schools and university, the education world. It's an online assessment system.
I would like a card that looks classy, and that is using the colors and the font of my logo.

I have attached:
1) my logo
2) A business card that I have designed quickly so you can have all the information required in the card, but I really don't like it.
3) The font that I am using (Lato Regular) to design my web platform
4) Some screenshots of my web platform so you can have a look at the style that I have.

Target Market(s)

Major market: Education system: Schools and university
Minor markets: Business in general

Industry/Entity Type

Business

Contact Information for Business Card

Clara Fenwick
Director

M: 0437 518 902
E: clara.fenwick@amberLoomSystems.com.au

Requirements
Must have
• The colors of my logo

```html
<!DOCTYPE html>
<html lang="en">
<head>
<meta charset="utf-8">
<title>Amber Loom Systems – Business Card</title>
<link href="https://fonts.googleapis.com/css2?family=Lato:wght@400;700&display=swap" rel="stylesheet">
<style>
  :root {
    --page-bg: #e9ecef;
    --card-white: #fbfbfc;
    --ink-blue: #1f5f9e;
    --band-blue: #0f73b3;
    --band-deep: #0a5c96;
    --swoosh-cyan: #6ccbe0;
    --text-grey: #3b4654;
    --accent-cyan: #3fb6da;
  }
  * { box-sizing: border-box; margin: 0; padding: 0; }
  html, body { width: 1200px; height: 780px; overflow: hidden; }
  body {
    background: var(--page-bg);
    font-family: "Lato", sans-serif;
    display: flex;
    align-items: center;
    justify-content: center;
    gap: 60px;
  }
  .card {
    position: relative;
    width: 525px;
    height: 306px;
    background: var(--card-white);
    border-radius: 14px;
    overflow: hidden;
    box-shadow: 0 10px 28px rgba(20, 40, 70, 0.18);
  }
  .card-art { position: absolute; inset: 0; width: 100%; height: 100%; }

  .brand {
    position: absolute;
    display: flex;
    align-items: center;
    gap: 12px;
  }
  .brand-square {
    width: 34px; height: 34px;
    background: var(--ink-blue);
    border-radius: 4px;
    flex: none;
  }
  .brand-name {
    color: var(--ink-blue);
    font-size: 22px;
    font-weight: 400;
    letter-spacing: 1px;
    white-space: nowrap;
  }

  /* Front */
  .card-front .brand { left: 34px; top: 152px; }

  .person { position: absolute; right: 30px; top: 24px; text-align: right; }
  .person-name { color: var(--ink-blue); font-size: 20px; font-weight: 400; line-height: 24px; }
  .person-role { color: var(--accent-cyan); font-size: 11px; margin-top: 1px; }

  .contact {
    position: absolute; right: 30px; top: 76px;
    list-style: none; text-align: right;
    color: var(--text-grey); font-size: 10.5px; line-height: 19px;
  }
  .contact li { display: flex; align-items: center; justify-content: flex-end; gap: 7px; white-space: nowrap; }
  .contact-icon {
    width: 13px; height: 13px; border-radius: 3px;
    background: var(--accent-cyan);
    display: inline-flex; align-items: center; justify-content: center;
    flex: none;
  }
  .contact-icon svg { width: 9px; height: 9px; }

  .web {
    position: absolute; right: 30px; bottom: 24px;
    color: #ffffff; font-size: 11px; letter-spacing: 0.3px;
  }

  /* Back */
  .card-back .brand {
    left: 50%; top: 50%;
    transform: translate(-50%, -50%);
  }
</style>
</head>
<body>

  <section class="card card-front" aria-label="Business card front">
    <svg class="card-art" viewBox="0 0 525 306" preserveAspectRatio="none" aria-hidden="true">
      <defs>
        <linearGradient id="frontBand" x1="0" y1="0" x2="1" y2="0">
          <stop offset="0" stop-color="#0a5c96"/>
          <stop offset="0.6" stop-color="#0f73b3"/>
          <stop offset="1" stop-color="#0a5c96"/>
        </linearGradient>
      </defs>
      <path d="M0,276 C170,268 360,230 525,150 L525,160 C370,240 180,286 0,294 Z" fill="#6ccbe0"/>
      <path d="M0,292 C180,284 370,238 525,162 L525,306 L0,306 Z" fill="url(#frontBand)"/>
    </svg>

    <div class="brand">
      <span class="brand-square"></span>
      <span class="brand-name">Amber Loom Systems</span>
    </div>

    <div class="person">
      <p class="person-name">Clara Fenwick</p>
      <p class="person-role">Director</p>
    </div>

    <ul class="contact">
      <li>0437 518 902
        <span class="contact-icon"><svg viewBox="0 0 10 10"><rect x="3" y="1" width="4" height="8" rx="1" fill="#fff"/></svg></span>
      </li>
      <li>clara.fenwick@amberLoomSystems.com.au
        <span class="contact-icon"><svg viewBox="0 0 10 10"><rect x="1" y="2.5" width="8" height="5" fill="#fff"/><path d="M1,2.5 L5,6 L9,2.5" stroke="#3fb6da" stroke-width="0.8" fill="none"/></svg></span>
      </li>
    </ul>

    <p class="web">www.amberloomsystems.com.au</p>
  </section>

  <section class="card card-back" aria-label="Business card back">
    <svg class="card-art" viewBox="0 0 525 306" preserveAspectRatio="none" aria-hidden="true">
      <defs>
        <linearGradient id="backBand" x1="0" y1="0" x2="1" y2="0">
          <stop offset="0" stop-color="#0a5c96"/>
          <stop offset="0.5" stop-color="#0f73b3"/>
          <stop offset="1" stop-color="#0a5c96"/>
        </linearGradient>
      </defs>
      <path d="M0,0 L525,0 L525,44 C360,60 170,76 0,66 Z" fill="url(#backBand)"/>
      <path d="M40,74 C200,80 360,66 525,50 L525,56 C360,76 200,88 40,74 Z" fill="#6ccbe0"/>
      <path d="M0,240 C170,230 360,246 525,262 L525,306 L0,306 Z" fill="url(#backBand)"/>
      <path d="M0,232 C170,220 360,236 490,252 C360,242 170,228 0,240 Z" fill="#6ccbe0"/>
    </svg>

    <div class="brand">
      <span class="brand-square"></span>
      <span class="brand-name">Amber Loom Systems</span>
    </div>
  </section>

</body>
</html>
```